Venture 482 - Lumora Book Cover

I am looking for a Lumora book cover for my book about "Venture 482".
The Book is Titled:
Venture 482 Ascended
Shaping Outcomes: Paths To Unlocking Cosmic Truths
Author is Dorian Pell
Here is a book description that may help you understand more about it:
Inspired by the genius of Edwin Marlowe, this comprehensive guide delves into the ancient wisdom and cutting-edge science behind the 482 method, a powerful tool for manifesting your desires. Whether you're seeking personal growth, financial success, or spiritual enlightenment, this book provides advanced techniques and methods to transform your dreams into reality.
Any questions please ask.
Thanks
Owen

```html
<!DOCTYPE html>
<html lang="en">
<head>
<meta charset="utf-8">
<title>Venture 482 Ascended — Book Cover</title>
<link href="https://fonts.googleapis.com/css2?family=Cinzel:wght@400;500&family=Cormorant+Garamond:wght@500&family=Tinos&display=swap" rel="stylesheet">
<style>
  :root {
    --backdrop: #e8e8e8;
    --space-deep: #120a24;
    --space-violet: #3a1d66;
    --glow-lilac: #a66ad6;
    --glow-ember: #c8641e;
    --ink-cream: #fbe9de;
  }
  * { margin: 0; padding: 0; box-sizing: border-box; }
  html, body {
    width: 1200px; height: 1131px; overflow: hidden;
    background: var(--backdrop);
  }
  .cover {
    position: absolute; left: 251px; top: 40px;
    width: 698px; height: 1051px;
    overflow: hidden; border-radius: 6px;
    background: var(--space-deep);
    color: var(--ink-cream);
    text-align: center;
  }
  .cover-art {
    position: absolute; inset: 0;
    background:
      radial-gradient(ellipse 40% 30% at 50% 52%, rgba(220,170,255,0.45), transparent 70%),
      radial-gradient(circle at 50% 50%, rgba(166,106,214,0.55) 0, rgba(90,40,150,0.35) 32%, transparent 55%),
      radial-gradient(ellipse 70% 18% at 50% 96%, rgba(200,100,30,0.55), transparent 75%),
      linear-gradient(180deg, #1c0f36 0%, var(--space-violet) 45%, #2a1548 75%, #140a22 100%);
  }
  .series {
    position: absolute; left: 0; right: 0; top: 240px;
    font-family: "Cinzel", serif; font-weight: 400;
    font-size: 104px; line-height: 1; letter-spacing: 1px;
  }
  .number {
    position: absolute; left: 0; right: 0; top: 360px;
    font-family: "Cormorant Garamond", serif; font-weight: 500;
    font-size: 330px; line-height: 1; letter-spacing: -14px;
  }
  .edition {
    position: absolute; left: 0; right: 0; top: 710px;
    font-family: "Cinzel", serif; font-size: 58px; line-height: 1;
    letter-spacing: 21px; padding-left: 21px;
  }
  .subtitle-lead {
    position: absolute; left: 0; right: 0; top: 802px;
    font-family: "Tinos", serif; font-size: 23px; line-height: 1;
    text-transform: uppercase;
  }
  .subtitle {
    position: absolute; left: 0; right: 0; top: 846px;
    font-family: "Tinos", serif; font-size: 22px; line-height: 33px;
  }
  .author {
    position: absolute; left: 0; right: 0; top: 952px;
    font-family: "Cinzel", serif; font-size: 42px; line-height: 1;
    letter-spacing: 13px; padding-left: 13px;
  }
</style>
</head>
<body>
  <main class="cover">
    <div class="cover-art" role="img" aria-label="Cosmic illustration: a meditating figure seated before a glowing sacred-geometry sphere in a starry violet nebula, with amber light below"></div>
    <h1>
      <span class="series">Venture</span>
      <span class="number">482</span>
      <span class="edition">ASCENDED</span>
    </h1>
    <p class="subtitle-lead">Shaping Outcomes:</p>
    <p class="subtitle">Paths to unlocking<br>cosmic truths</p>
    <p class="author">DORIAN PELL</p>
  </main>
</body>
</html>
```